HVAC Parts Distributor Website

We are working with an HVAC parts distributor to design a website. They primarily work with HVAC contractors.
They are similar to: https://www.corvelparts.example, and https://www.ductmart.example
Thank you for taking the time to consider designing a website for us. We are web developers based in Stockton, CA, USA. Most of our projects go through the same process. Understanding this process may help you win a project with us. We custom-code all of our websites in-house. We don’t have any requirements as to what tools you use for your design, but we ask that you follow these guidelines.
IMAGES:
If you use any images or icons in the design, we ask that you have a link to the asset so we can purchase the image/icon. Most of the designs we submit do not have the customer’s images on them unless they have some great images. Be creative; show us the feeling you are trying to portray with your image choices. Use any royalty-free site you choose. We subscribe to Quillon and mainly use their images, but we can purchase images outside of Quillon.
FONTS:
We ask that you identify the fonts you’re using in the design. This can be done in a message if you want. We typically use Brevix Fonts and Quillon Fonts.
CONTENT:
We're always open to different content and ideas. We often submit designs with stock images so the client can see our vision. We typically take pictures after the website launch to use their images with our vision. Lorem Ipsum is fine for paragraphs, but we ask that you make the Headers with correct English. We want to be able to show the vision and identify the sections of the website.
INSPIRATION:
We typically add a couple of links in the brief of websites we like to help you get started in your design.
REVISIONS:
We do not often ask for revisions of the designs unless we see something in the design that may not appeal to the client. If there are slight changes that we want to make, we simply do that in the development process.
FEEDBACK:
We rarely give feedback on designs during the design process. We are working on many website projects and do not have the time to give feedback. We usually respond if your request is well thought out and asks specific questions, but a note asking “feedback, please” usually goes unanswered.

```html
<!DOCTYPE html>
<html lang="en">
<head>
<meta charset="utf-8">
<title>Keystream HVAC Distribution</title>
<link href="https://fonts.googleapis.com/css2?family=Poppins:ital,wght@0,400;0,500;0,600;0,700;0,800;1,400&display=swap" rel="stylesheet">
<style>
:root{
  --green:#8fa80c;
  --green-dark:#7d9309;
  --ink:#1c1c1c;
  --black:#0d0b0b;
  --footer-top:#160e0e;
  --footer:#2e2e2e;
  --footer-bottom:#232323;
  --text:#3a3a3a;
  --muted:#6b6b6b;
  --line:#d6d6d6;
  --soft:#f3f3f3;
  --white:#fff;
}
*{margin:0;padding:0;box-sizing:border-box}
html,body{width:1200px;height:3531px;overflow:hidden}
body{font-family:'Poppins',sans-serif;color:var(--text);background:var(--white);position:relative}
.abs{position:absolute}
a{color:inherit;text-decoration:none}

/* header */
.site-header{position:absolute;left:0;top:0;width:1200px;height:104px;background:var(--white)}
.brand{position:absolute;left:74px;top:24px;text-align:center}
.brand-name{font-weight:800;font-size:40px;line-height:44px;letter-spacing:1px;color:var(--ink)}
.brand-sub{font-weight:500;font-size:15px;letter-spacing:1.5px;color:#7a7a7a;line-height:20px}
.search{position:absolute;left:374px;top:29px;width:437px;height:53px;border:1px solid var(--line);display:flex}
.search span{flex:1;font-size:13px;padding:17px 15px;color:#333}
.search .search-btn{width:78px;background:var(--green);display:flex;align-items:center;justify-content:center}
.top-links{position:absolute;left:836px;top:47px;font-size:12.5px;font-weight:500;color:#222;letter-spacing:.3px}

.main-nav{position:absolute;left:0;top:104px;width:1200px;height:62px;background:var(--black)}
.main-nav a{position:absolute;top:22px;font-size:14.5px;font-weight:700;color:var(--white);letter-spacing:.3px}
.main-nav a.active{color:var(--green)}

/* hero */
.hero{position:absolute;left:0;top:166px;width:1200px;height:645px;background:linear-gradient(90deg,#8a6552 0%,#b9b8b2 25%,#c8c7c2 45%,#9a8f86 70%,#6f5547 100%)}
.hero-title{position:absolute;left:0;width:1200px;text-align:center;color:var(--white);font-weight:800;line-height:1}
.btn{display:flex;align-items:center;justify-content:center;font-weight:700;color:var(--white);letter-spacing:.3px}
.dots{position:absolute;left:559px;display:flex;gap:11px}
.dots i{width:13px;height:13px;background:var(--black);display:block}
.dots i:first-child{background:var(--white)}

/* categories */
.cat{position:absolute;top:863px;width:244px;height:175px;border:1px solid var(--line);text-align:center}
.cat .ph{width:110px;height:85px;margin:18px auto 0;border-radius:8px}
.cat h3{font-size:17px;font-weight:600;color:var(--ink);margin-top:16px}
.arrow{position:absolute;width:20px;height:20px;border-radius:50%;display:flex;align-items:center;justify-content:center}
.arrow.off{background:#c5c5c5}
.arrow.on{background:var(--green)}

/* about */
.about-heading{position:absolute;left:74px;top:1182px;color:var(--white);font-weight:700;font-size:33px;line-height:38px}
.about-text{position:absolute;left:74px;top:1268px;width:460px;color:var(--white);font-size:17.5px;line-height:30.5px}

/* why */
.section-title{position:absolute;left:0;width:1200px;text-align:center;font-weight:700;color:var(--ink);font-size:31px;letter-spacing:.3px}
.why{position:absolute;top:1812px;width:250px;text-align:center}
.why .ring{width:101px;height:101px;border-radius:50%;border:1px solid #cfcfcf;margin:0 auto;display:flex;align-items:center;justify-content:center}
.why .ring span{width:78px;height:78px;border-radius:50%;background:var(--green);display:flex;align-items:center;justify-content:center}
.why h3{color:var(--green);font-size:22px;font-weight:700;margin-top:20px}
.why p{font-size:15.5px;line-height:27px;color:#444;margin-top:10px}

.brands{position:absolute;left:0;top:2132px;width:1200px;height:248px;background:var(--soft)}
.brand-mark{position:absolute;top:2276px;font-size:21px;font-weight:600;color:#2a2a2a;transform:translateX(-50%);white-space:nowrap}

/* testimonials */
.quote-card{position:absolute;top:2508px;width:330px;height:296px;border:1px solid var(--line);text-align:center}
.quote-card .mark{color:var(--green);font-size:56px;font-weight:800;line-height:40px;margin-top:30px;height:40px}
.quote-card p{font-style:italic;font-size:17.5px;line-height:30px;color:#333;margin:12px 22px 0}
.quote-card h4{font-size:15px;font-weight:600;color:var(--ink);margin-top:12px}
.avatar{position:absolute;top:2758px;width:92px;height:92px;border-radius:50%;border:3px solid var(--white);background:linear-gradient(160deg,#b9c2cc,#5f6670)}

/* footer */
.footer-top{position:absolute;left:0;top:2945px;width:1200px;height:142px;background:var(--footer-top)}
.contact-ico{position:absolute;top:2991px;width:48px;height:48px;border:1px solid #6a6a6a;border-radius:50%;display:flex;align-items:center;justify-content:center}
.contact-label{position:absolute;color:var(--green);font-weight:600;font-size:18px}
.contact-val{position:absolute;color:var(--white);font-size:14.5px;line-height:24px}
.footer{position:absolute;left:0;top:3087px;width:1200px;height:379px;background:var(--footer)}
.fcol{position:absolute;top:3143px;color:var(--white)}
.fcol h4{font-size:18px;font-weight:700;letter-spacing:.3px;margin-bottom:16px}
.fcol a{display:block;font-size:15px;line-height:44.3px;color:#eaeaea}
.fcol p{font-size:15px;line-height:29px;color:#eaeaea;width:260px}
.subscribe-input{position:absolute;left:870px;top:3261px;width:256px;height:53px;background:var(--white);font-size:14px;color:#333;padding:17px 16px}
.subscribe-btn{position:absolute;left:870px;top:3322px;width:256px;height:52px;background:var(--green);font-size:16px}
.footer-bottom{position:absolute;left:0;top:3466px;width:1200px;height:65px;background:var(--footer-bottom)}
.copyright{position:absolute;left:74px;top:3492px;font-size:13px;color:#d8d8d8}
.social{position:absolute;top:3489px;width:22px;height:22px;background:#d8d8d8;border-radius:3px}
</style>
</head>
<body>

<header class="site-header">
  <div class="brand">
    <div class="brand-name">KEYSTREAM</div>
    <div class="brand-sub">-HVAC DISTRIBUTION-</div>
  </div>
  <div class="search">
    <span>Search for products</span>
    <div class="search-btn">
      <svg width="18" height="18" viewBox="0 0 18 18"><circle cx="7.5" cy="7.5" r="5" fill="none" stroke="#fff" stroke-width="2.4"/><line x1="11.3" y1="11.3" x2="15.5" y2="15.5" stroke="#fff" stroke-width="2.6" stroke-linecap="round"/></svg>
    </div>
  </div>
  <div class="top-links">REQUEST ACCOUNT &nbsp;/&nbsp; CONTRACTOR TOOLS</div>
</header>

<nav class="main-nav">
  <a class="active" style="left:74px">HOME</a>
  <a style="left:162px">ABOUT US</a>
  <a style="left:281px">PRODUCT DISTRIBUTIONS</a>
  <a style="left:516px">RESOURCES</a>
  <a style="left:648px">BLOG</a>
  <a style="left:731px">TESTIMONIALS</a>
  <a style="left:885px">CONTACT US</a>
  <a style="left:1049px;font-size:13px;top:23px;font-weight:600">
    <svg width="14" height="14" viewBox="0 0 14 14" style="vertical-align:-2px;margin-right:8px"><circle cx="7" cy="4" r="3.2" fill="#8fa80c"/><path d="M1 14c0-4 3-6 6-6s6 2 6 6z" fill="#8fa80c"/></svg>SIGN IN</a>
</nav>

<section class="hero" role="img" aria-label="Technician in a hard hat servicing an outdoor air conditioning condenser against a brick wall">
  <div class="hero-title" style="top:218px;font-size:64px;letter-spacing:1px">WELCOME TO KEYSTREAM</div>
  <div class="hero-title" style="top:280px;font-size:60px;font-weight:700">HVAC Distribution</div>
  <a class="btn abs" style="left:517px;top:365px;width:165px;height:52px;background:var(--green);font-size:16px">READ MORE</a>
  <div class="dots" style="top:580px"><i></i><i></i><i></i><i></i></div>
</section>

<section>
  <div class="arrow off" style="left:40px;top:941px"><svg width="10" height="10" viewBox="0 0 10 10"><path d="M6 1 2 5l4 4M2 5h7" stroke="#fff" stroke-width="1.8" fill="none"/></svg></div>
  <div class="cat" style="left:74px"><div class="ph" role="img" aria-label="Packaged HVAC unit" style="background:linear-gradient(160deg,#6e6e6e,#1f1f1f)"></div><h3>HVAC Equipment</h3></div>
  <div class="cat" style="left:344px"><div class="ph" role="img" aria-label="Circulator pump part" style="background:radial-gradient(circle,#c9c9c9,#555 75%,transparent 76%)"></div><h3>HVACR Parts</h3></div>
  <div class="cat" style="left:614px"><div class="ph" role="img" aria-label="Brass plumbing fittings" style="background:linear-gradient(160deg,#e8c25a,#a6781c)"></div><h3>Hydronics &amp; Plumbing</h3></div>
  <div class="cat" style="left:884px"><div class="ph" role="img" aria-label="Refrigeration valve" style="background:linear-gradient(180deg,#bdbdbd,#4c4c4c);width:60px"></div><h3>Refrigeration</h3></div>
  <div class="arrow on" style="left:1140px;top:941px"><svg width="10" height="10" viewBox="0 0 10 10"><path d="M4 1l4 4-4 4M8 5H1" stroke="#fff" stroke-width="1.8" fill="none"/></svg></div>
</section>

<section>
  <svg class="abs" style="left:0;top:1120px" width="1200" height="551" viewBox="0 0 1200 551">
    <polygon points="0,0 713,0 525,506 0,506" fill="#8fa80c"/>
  </svg>
  <svg class="abs" style="left:0;top:1120px" width="1200" height="551" viewBox="0 0 1200 551" role="img" aria-label="Technician holding a refrigerant manifold gauge set with coloured hoses">
    <defs><linearGradient id="gaugeShot" x1="0" y1="0" x2="1" y2="1"><stop offset="0" stop-color="#8a6a4a"/><stop offset=".5" stop-color="#c8b79a"/><stop offset="1" stop-color="#6f8f5a"/></linearGradient></defs>
    <polygon points="668,46 1200,46 1200,551 525,551" fill="url(#gaugeShot)"/>
  </svg>
  <h2 class="about-heading">WELCOME TO KEYSTREAM<br>HVAC DISTRIBUTION</h2>
  <p class="about-text">Sed ut perspiciatis unde omnis iste natus error sit voluptatem accusantium doloremque laudantium, totam rem aperiam, eaque ipsa quae ab illo inventore veritatis et quasi architecto beatae vitae dicta sunt explicabo. Nemo enim ipsam voluptatem quia voluptas sit aspernatur aut odit aut fugit, sed quia consequuntur magni ...</p>
  <a class="btn abs" style="left:74px;top:1505px;width:166px;height:54px;background:var(--black);font-size:16px">READ MORE</a>
</section>

<section>
  <h2 class="section-title" style="top:1730px">WHY CHOOSE KEYSTREAM HVAC DISTRIBUTION</h2>
  <div class="why" style="left:70px">
    <div class="ring"><span><svg width="34" height="26" viewBox="0 0 34 26"><rect x="1" y="4" width="20" height="14" rx="2" fill="#fff"/><path d="M21 8h7l5 6v4H21z" fill="#fff"/><circle cx="8" cy="20" r="4" fill="#fff" stroke="#8fa80c" stroke-width="2"/><circle cx="26" cy="20" r="4" fill="#fff" stroke="#8fa80c" stroke-width="2"/></svg></span></div>
    <h3>Free Shipping</h3>
    <p>Sed ut perspiciatis unde omnis iste natus error sit voluptatem accusantium dolore.</p>
  </div>
  <div class="why" style="left:338px">
    <div class="ring"><span><svg width="34" height="22" viewBox="0 0 34 22"><rect x="1" y="2" width="32" height="18" rx="2" fill="#fff"/><circle cx="17" cy="11" r="5" fill="#8fa80c"/></svg></span></div>
    <h3>Lower Prices</h3>
    <p>Sed ut perspiciatis unde omnis iste natus error sit voluptatem accusantium dolore.</p>
  </div>
  <div class="why" style="left:612px">
    <div class="ring"><span><svg width="28" height="24" viewBox="0 0 28 24"><path d="M10 2 2 10l8 8v-5c7 0 12 2 15 8 0-9-5-14-15-15z" fill="#fff"/></svg></span></div>
    <h3>Free Return</h3>
    <p>Sed ut perspiciatis unde omnis iste natus error sit voluptatem accusantium dolore.</p>
  </div>
  <div class="why" style="left:881px">
    <div class="ring"><span><svg width="34" height="28" viewBox="0 0 34 28"><circle cx="12" cy="16" r="8" fill="none" stroke="#fff" stroke-width="5" stroke-dasharray="4 2.3"/><circle cx="25" cy="8" r="5" fill="none" stroke="#fff" stroke-width="4" stroke-dasharray="3 2"/></svg></span></div>
    <h3>Exclusive Gear</h3>
    <p>Sed ut perspiciatis unde omnis iste natus error sit voluptatem accusantium dolore.</p>
  </div>
</section>

<section>
  <div class="brands"></div>
  <h2 class="section-title" style="top:2188px">TRUSTED BRANDS</h2>
  <span class="brand-mark" style="left:148px">Finlow</span>
  <span class="brand-mark" style="left:297px">Casora</span>
  <span class="brand-mark" style="left:441px">Pipera</span>
  <span class="brand-mark" style="left:578px">Holt &amp; Vane</span>
  <span class="brand-mark" style="left:747px">Brightmoor</span>
  <span class="brand-mark" style="left:897px">Quorvel</span>
  <span class="brand-mark" style="left:1044px">Ironcrest</span>
</section>

<section>
  <h2 class="section-title" style="top:2432px">TESTIMONIALS</h2>
  <div class="arrow off" style="left:40px;top:2646px"><svg width="10" height="10" viewBox="0 0 10 10"><path d="M6 1 2 5l4 4M2 5h7" stroke="#fff" stroke-width="1.8" fill="none"/></svg></div>
  <div class="quote-card" style="left:74px"><div class="mark">&rdquo;</div><p>&ldquo; Excepteur sint occaecat cupidatat non proident, sunt in culpa qui officia deserunt mollit anim id est laborum..&rdquo;</p><h4>Name Heading</h4></div>
  <div class="quote-card" style="left:436px"><div class="mark">&rdquo;</div><p>&ldquo; Excepteur sint occaecat cupidatat non proident, sunt in culpa qui officia deserunt mollit anim id est laborum..&rdquo;</p><h4>Name Heading</h4></div>
  <div class="quote-card" style="left:797px"><div class="mark">&rdquo;</div><p>&ldquo; Excepteur sint occaecat cupidatat non proident, sunt in culpa qui officia deserunt mollit anim id est laborum..&rdquo;</p><h4>Name Heading</h4></div>
  <div class="avatar" role="img" aria-label="Customer portrait" style="left:193px"></div>
  <div class="avatar" role="img" aria-label="Customer portrait" style="left:555px"></div>
  <div class="avatar" role="img" aria-label="Customer portrait" style="left:916px"></div>
  <div class="arrow on" style="left:1140px;top:2646px"><svg width="10" height="10" viewBox="0 0 10 10"><path d="M4 1l4 4-4 4M8 5H1" stroke="#fff" stroke-width="1.8" fill="none"/></svg></div>
</section>

<footer>
  <div class="footer-top"></div>
  <div class="abs" style="left:74px;top:2988px;text-align:center">
    <div style="font-weight:800;font-size:36px;line-height:40px;color:#7f8a3a;letter-spacing:1px">KEYSTREAM</div>
    <div style="font-size:14px;letter-spacing:1.5px;color:#8a8a8a;font-weight:500">-HVAC DISTRIBUTION-</div>
  </div>
  <div class="contact-ico" style="left:349px"><svg width="16" height="14" viewBox="0 0 16 14"><path d="M0 2l5-2 6 2 5-2v12l-5 2-6-2-5 2z" fill="#8fa80c"/></svg></div>
  <div class="contact-label" style="left:414px;top:2970px">Address</div>
  <div class="contact-val" style="left:414px;top:2998px">Nemo enim ipsam volup<br>tatem quia</div>
  <div class="contact-ico" style="left:640px"><svg width="14" height="14" viewBox="0 0 14 14"><path d="M3 1l3 3-2 2c1 2 2 3 4 4l2-2 3 3-2 2C6 13 1 8 1 3z" fill="#8fa80c"/></svg></div>
  <div class="contact-label" style="left:704px;top:2988px">Phone</div>
  <div class="contact-val" style="left:704px;top:3016px">+1-88-888-8888</div>
  <div class="contact-ico" style="left:873px"><svg width="14" height="11" viewBox="0 0 14 11"><rect width="14" height="11" rx="1" fill="#8fa80c"/><path d="M1 1l6 5 6-5" stroke="#160e0e" stroke-width="1.3" fill="none"/></svg></div>
  <div class="contact-label" style="left:938px;top:2988px">Email</div>
  <div class="contact-val" style="left:938px;top:3016px">info@companyname.com</div>

  <div class="footer"></div>
  <div class="fcol" style="left:74px"><h4>CUSTOMER SERVICES</h4><a>Order Status</a><a>Contact Us</a><a>Shipping Policy</a><a>Returns</a><a>FAQs</a></div>
  <div class="fcol" style="left:380px"><h4>ABOUT US</h4><a>Meet The Team</a><a>Careers</a><a>Our Blog</a></div>
  <div class="fcol" style="left:619px"><h4>RESOURCES</h4><a>Reorder</a><a>Quick Order</a><a>Saved Carts</a><a>Project Calculators</a><a>Video Library</a></div>
  <div class="fcol" style="left:870px"><h4>SUBSCRIBE US</h4><p>Stay in the know with top brands &amp; product spotlights!</p></div>
  <div class="subscribe-input">Email Address</div>
  <a class="btn subscribe-btn">Subscribe</a>

  <div class="footer-bottom"></div>
  <div class="copyright">Copyright &copy;2023 by Company Name All Right Reserved</div>
  <span class="social" style="left:971px" aria-label="Social link"></span>
  <span class="social" style="left:1014px" aria-label="Social link"></span>
  <span class="social" style="left:1058px" aria-label="Social link"></span>
  <span class="social" style="left:1101px" aria-label="Social link"></span>
</footer>

</body>
</html>
```